Healthcare/Medical Consultant Company

QRN is a Healthcare Conultant Company. We help doctors manage the business side of their medical practice.
We already have a very basic world press design. We want an upgraded design that conveys partnership, healthcare expertise and healthcare innovation to our client. It needs to have a sleek, clean, modern and inclusive look. Pictures need need to convey diversity (including pictures of people of all races and shows both men and women working together in a healthcare environment to make it better). The Pictures on the home page should particularly illustrate diversity and Healthcare expertise. The company logo is blue and white but the site doesn’t have to follow the exact same theme but the logo needs to blend well with the chosen theme. The logo should ideally be in the header of the website. We would also like the following included in our website:

1. Pages should include: a home page, About Us page, Services page, Get a quote page, Contact Us page, Staff page(where we can add pictures and bio for staff).

2. The Drop down menu for services should have hyperlinks ( for each service)Leading to a page that provides detailed info about that specific service. Our services include: Revenue Cycle Management, Regulatory Compliance, Human Resources Management, & practice Management.

3. Links to social media should in the header or footer of each page.

4. Contact info should be in the footer of each page.

5. Clients should be an email to us from the contact page.

Target Market(s)

Physician Medical Practices

Industry/Entity Type

Medical

Coding

Coded - Design and coding required

Font styles to use
Sans Serif

Colors

Designer to choose colors to be used in the design.

Requirements
Must have
• See project description
Nice to have
• See project description

```html
<!DOCTYPE html>
<html lang="en">
<head>
<meta charset="utf-8">
<title>QRN – Allied Practice Partners</title>
<link rel="stylesheet" href="https://fonts.googleapis.com/css2?family=Cinzel:wght@400;700&family=Open+Sans:wght@400;600;700&display=swap">
<style>
:root{
  --navy:#0b3d91;
  --navy-deep:#093480;
  --sky:#2b8fd3;
  --ink:#222;
  --muted:#666;
  --pale:#f2f9fc;
  --line:#c9dbe3;
  --white:#fff;
}
*{box-sizing:border-box;margin:0;padding:0}
html,body{width:1200px;height:3041px;overflow:hidden;background:var(--white)}
body{position:relative;font-family:"Open Sans",Arial,sans-serif;color:var(--ink)}
.abs{position:absolute}

/* header */
.brand{left:98px;top:50px;display:flex;align-items:center;gap:10px;font-family:"Open Sans",Arial,sans-serif;font-weight:600;font-size:17px;color:var(--navy);white-space:nowrap}
.brand-dot{width:22px;height:22px;border-radius:50%;background:var(--navy);flex:none}
.topbar{right:98px;top:22px;font-size:15px;color:#333;display:flex;align-items:center;gap:12px}
.topbar svg{width:14px;height:14px;fill:var(--sky);margin-right:6px;vertical-align:-2px}
.nav{right:98px;top:68px;display:flex;gap:32px;font-family:"Cinzel",Georgia,serif;font-size:16px;color:#111;align-items:center}
.nav .active{color:var(--sky)}
.nav svg{width:16px;height:16px}
.dropdown{left:640px;top:114px;width:254px;background:var(--white);padding:16px 0;z-index:3;box-shadow:0 2px 6px rgba(0,0,0,.12)}
.dropdown li{list-style:none;font-size:15px;color:#333;padding:0 28px;line-height:35px}

/* hero */
.hero{left:0;top:114px;width:1200px;height:620px;background:linear-gradient(110deg,#cfd6d8 0%,#b9b1a4 40%,#8a7766 70%,#6a5b4f 100%)}
.hero-kicker{left:100px;top:318px;font-size:35px;color:var(--white);font-family:"Cinzel",Georgia,serif}
.hero-title{left:100px;top:368px;font-size:58px;color:var(--white);font-family:"Cinzel",Georgia,serif;font-weight:700}
.btn-outline{left:100px;top:472px;width:196px;height:58px;border:2px solid var(--white);border-radius:30px;color:var(--white);font-weight:700;font-size:16px;display:flex;align-items:center;justify-content:center;letter-spacing:.5px}
.dots{left:566px;top:588px;display:flex;gap:4px}
.dots span{width:13px;height:13px;border:2px solid var(--white);border-radius:50%}
.dots span.on{background:var(--white)}

/* section headings */
.section-title{left:0;width:1200px;text-align:center;font-family:"Cinzel",Georgia,serif;font-weight:400;font-size:40px;line-height:54px;color:#111}
.intro{left:196px;top:894px;width:808px;text-align:center;font-size:14.5px;line-height:27px;color:var(--muted)}
.video{left:400px;top:1044px;width:400px;height:258px;background:linear-gradient(120deg,#9b8a6d,#d9d2c3 55%,#f1ede4)}
.play{left:572px;top:1145px;width:56px;height:56px;border-radius:50%;background:#111;display:flex;align-items:center;justify-content:center}
.btn-fill{left:525px;top:1350px;width:150px;height:62px;border-radius:31px;background:var(--sky);color:var(--white);font-weight:700;font-size:17px;display:flex;align-items:center;justify-content:center}

/* services */
.services-bg{left:0;top:1470px;width:1200px;height:670px;background:var(--pale)}
.card{top:1685px;width:318px;height:312px;background:var(--white);box-shadow:0 0 6px rgba(0,0,0,.18);text-align:center;padding-top:36px}
.card svg{width:58px;height:58px;fill:var(--navy)}
.card h3{font-family:"Cinzel",Georgia,serif;font-weight:400;font-size:23px;line-height:33px;margin-top:18px;color:#111}
.card p{font-size:14px;line-height:26px;color:var(--muted);margin:12px 16px 0}
.card a{display:block;margin-top:18px;font-weight:700;font-size:15px;color:var(--sky);text-decoration:none}
.arrow{top:1817px;width:48px;height:48px;border:1px solid #555;border-radius:50%;background:var(--white);display:flex;align-items:center;justify-content:center}
.arrow svg{width:20px;height:20px;stroke:#333;fill:none;stroke-width:2}

/* blog */
.post-img{top:2282px;width:222px;height:188px;border:1px solid #ddd;padding:5px;background:var(--white)}
.post-img div{width:100%;height:100%}
.post{top:2280px;width:250px}
.post h4{font-size:19px;font-weight:600;color:#111}
.post .meta{font-size:12.5px;color:#444;margin-top:12px}
.post .meta svg{width:11px;height:11px;fill:var(--navy);vertical-align:-1px;margin-right:5px}
.post p{font-size:14px;line-height:24px;color:var(--muted);margin-top:10px}
.post a{display:block;margin-top:16px;font-weight:700;font-size:14px;color:var(--sky);text-decoration:none}

/* footer */
.footer{left:0;top:2560px;width:1200px;height:481px;background:var(--navy)}
.f-brand{left:60px;top:2770px;width:330px;display:flex;align-items:center;justify-content:center;gap:10px;color:var(--white);font-family:"Open Sans",Arial,sans-serif;font-weight:600;font-size:17px;white-space:nowrap}
.f-brand .brand-dot{background:var(--white)}
.socials{left:145px;top:2847px;display:flex;gap:9px}
.socials span{width:34px;height:34px;border:1.5px solid var(--white);border-radius:50%}
.f-head{top:2710px;font-family:"Cinzel",Georgia,serif;font-size:19px;color:var(--white)}
.f-list{left:424px;top:2750px;list-style:none;font-size:13.5px;line-height:26px;color:var(--white)}
.f-contact{left:593px;top:2750px;font-size:13.5px;color:var(--white);line-height:22px}
.f-contact div{display:flex;gap:14px;margin-bottom:26px}
.f-contact svg{width:14px;height:14px;fill:var(--white);flex:none;margin-top:4px}
.f-sub{left:825px;top:2750px;width:276px;font-size:12.5px;color:var(--white);white-space:nowrap}
.f-sub .field{margin-top:20px;height:36px;background:var(--white);border:1px solid #ccc;color:#666;font-size:12.5px;padding:9px 12px}
.f-sub .btn{margin-top:22px;width:106px;height:36px;border-radius:18px;background:var(--sky);color:var(--white);font-weight:700;font-size:12.5px;display:flex;align-items:center;justify-content:center}
.f-rule{left:98px;top:2950px;width:1004px;height:1px;background:rgba(255,255,255,.35)}
.copy{left:0;top:2982px;width:1200px;text-align:center;font-size:13px;color:var(--white)}
</style>
</head>
<body>

<header>
  <div class="abs brand"><span class="brand-dot"></span>QRN Allied Practice Partners LLC</div>
  <div class="abs topbar">
    <span><svg viewBox="0 0 24 24"><path d="M6.6 10.8a15 15 0 0 0 6.6 6.6l2.2-2.2a1 1 0 0 1 1-.25 11 11 0 0 0 3.6.6 1 1 0 0 1 1 1V20a1 1 0 0 1-1 1A17 17 0 0 1 3 4a1 1 0 0 1 1-1h3.5a1 1 0 0 1 1 1 11 11 0 0 0 .6 3.6 1 1 0 0 1-.25 1z"/></svg>(555) 204-1187</span>
    <span>|</span>
    <span><svg viewBox="0 0 24 24"><path d="M2 5h20v14H2zm2 2v.5l8 5 8-5V7z"/></svg>info@alliedpracticegroup.com</span>
  </div>
  <nav class="abs nav">
    <span>Home</span><span>About Us</span><span class="active">Services</span><span>Get a Quote</span><span>Contact Us</span><span>Staff</span>
    <svg viewBox="0 0 24 24" fill="none" stroke="#111" stroke-width="3"><circle cx="10" cy="10" r="6.5"/><path d="M15 15l6 6"/></svg>
  </nav>
  <ul class="abs dropdown">
    <li>Revenue Cycle Management</li><li>Medical Billing &amp; Coding</li><li>Regulatory Compliance</li><li>Human Resources Training</li><li>Staff Education and Training</li>
  </ul>
</header>

<section>
  <div class="abs hero" role="img" aria-label="Photo of a doctor with a tablet talking with a smiling couple in a bright clinic"></div>
  <div class="abs hero-kicker">Allied Practice Partners</div>
  <div class="abs hero-title">Advancing Healthcare</div>
  <div class="abs btn-outline">GET A QUOTE</div>
  <div class="abs dots"><span class="on"></span><span></span><span></span><span></span></div>
  <svg class="abs" style="left:0;top:640px" width="1200" height="100" viewBox="0 0 1200 100">
    <path d="M0 60 Q600 -30 1200 60 L1200 100 L0 100Z" fill="#0b3d91"/>
    <path d="M0 86 Q600 -4 1200 86 L1200 100 L0 100Z" fill="#fff"/>
  </svg>
</section>

<section>
  <h1 class="abs section-title" style="top:756px">Welcome to<br>Allied Practice Partners</h1>
  <p class="abs intro">Allied Practice Partners (QRN) is a healthcare consulting firm skilled at helping physician practices advance their strategic vision in an ever-evolving healthcare system. Allied Practice Partners specializes in revenue cycle optimization, practice management improvement and developing new physician practices. Our technical skills allow us to dig deep into your revenue cycle while our strategic approach ensures we're keeping our eyes on the entire financial picture.</p>
  <div class="abs video" role="img" aria-label="Video still of a consultant reviewing documents with a physician"></div>
  <div class="abs play"><svg width="22" height="24" viewBox="0 0 22 24"><path d="M4 2l16 10L4 22z" fill="#fff"/></svg></div>
  <div class="abs btn-fill">ABOUT US</div>
</section>

<section>
  <div class="abs services-bg"></div>
  <svg class="abs" style="left:0;top:1460px" width="1200" height="80" viewBox="0 0 1200 80">
    <path d="M0 0 L1200 0 L1200 10 Q600 90 0 10Z" fill="#fff"/>
    <path d="M0 10 Q600 90 1200 10" stroke="#c9dbe3" stroke-width="6" fill="none"/>
  </svg>
  <svg class="abs" style="left:0;top:2070px" width="1200" height="80" viewBox="0 0 1200 80">
    <path d="M0 66 Q600 -10 1200 66 L1200 80 L0 80Z" fill="#fff"/>
    <path d="M0 66 Q600 -10 1200 66" stroke="#c9dbe3" stroke-width="6" fill="none"/>
  </svg>
  <h2 class="abs section-title" style="top:1592px">Our Services</h2>

  <div class="abs arrow" style="left:26px"><svg viewBox="0 0 24 24"><path d="M15 5l-7 7 7 7"/></svg></div>
  <div class="abs arrow" style="left:1127px"><svg viewBox="0 0 24 24"><path d="M9 5l7 7-7 7"/></svg></div>

  <article class="abs card" style="left:98px">
    <svg viewBox="0 0 24 24"><circle cx="12" cy="6" r="3"/><circle cx="5" cy="8" r="2.4"/><circle cx="19" cy="8" r="2.4"/><path d="M7 20v-4a5 5 0 0 1 10 0v4z"/><path d="M1 18v-3a4 4 0 0 1 5.5-3.7A6 6 0 0 0 5.8 14v4zM23 18v-3a4 4 0 0 0-5.5-3.7 6 6 0 0 1 .7 2.7v4z"/></svg>
    <h3>Revenue<br>Cycle Management</h3>
    <p>Nam libero tempore, cum soluta nobis est eligendi optio cumque nihil imped</p>
    <a>READ MORE</a>
  </article>
  <article class="abs card" style="left:441px">
    <svg viewBox="0 0 24 24"><path d="M4 1h16v22H4zm2 2v5h12V3zm0 7v2h2.5v-2zm4.5 0v2H13v-2zm4.5 0v2h3v-2zM6 14v2h2.5v-2zm4.5 0v2H13v-2zm4.5 0v2h3v-2zM6 18v2h2.5v-2zm4.5 0v2H13v-2zm4.5 0v2h3v-2z"/></svg>
    <h3>Medical<br>Billing &amp; Coding</h3>
    <p>Nam libero tempore, cum soluta nobis est eligendi optio cumque nihil imped</p>
    <a>READ MORE</a>
  </article>
  <article class="abs card" style="left:781px">
    <svg viewBox="0 0 24 24"><path d="M12 1L23 22H1zm-1.3 7v7h2.6V8zm0 9v2.6h2.6V17z"/></svg>
    <h3>Regulatory<br>Compliance</h3>
    <p>Nam libero tempore, cum soluta nobis est eligendi optio cumque nihil imped</p>
    <a>READ MORE</a>
  </article>
</section>

<section>
  <h2 class="abs section-title" style="top:2184px">Latest Blog</h2>

  <div class="abs post-img" style="left:96px"><div role="img" aria-label="Photo of a stethoscope and calculator on billing paperwork" style="background:linear-gradient(135deg,#3c4a55,#b8c3cb 55%,#e8ecef)"></div></div>
  <article class="abs post" style="left:343px">
    <h4>Finibus Bonoret Malorum</h4>
    <div class="meta"><svg viewBox="0 0 24 24"><path d="M3 4h18v18H3zm2 6v10h14V10zM7 1h2v4H7zm8 0h2v4h-2z"/></svg>17/08/2017 &nbsp;| &nbsp;<svg viewBox="0 0 24 24"><circle cx="12" cy="7" r="5"/><path d="M3 23a9 9 0 0 1 18 0z"/></svg>Dana Reyes</div>
    <p>Ut enim ad minima veniam, quis nos trum exercitationem ullam corporisu scipit laboriosam, nisi.</p>
    <a>READ MORE</a>
  </article>

  <div class="abs post-img" style="left:615px"><div role="img" aria-label="Photo of hands reviewing charts on a desk" style="background:linear-gradient(135deg,#e9e6df,#c9b49a 55%,#8c7a66)"></div></div>
  <article class="abs post" style="left:864px">
    <h4>Finibus Bonoret Malorum</h4>
    <div class="meta"><svg viewBox="0 0 24 24"><path d="M3 4h18v18H3zm2 6v10h14V10zM7 1h2v4H7zm8 0h2v4h-2z"/></svg>17/08/2017 &nbsp;| &nbsp;<svg viewBox="0 0 24 24"><circle cx="12" cy="7" r="5"/><path d="M3 23a9 9 0 0 1 18 0z"/></svg>Dana Reyes</div>
    <p>Ut enim ad minima veniam, quis nos trum exercitationem ullam corporisu scipit laboriosam, nisi.</p>
    <a>READ MORE</a>
  </article>
</section>

<footer>
  <div class="abs footer"></div>
  <svg class="abs" style="left:0;top:2555px" width="1200" height="80" viewBox="0 0 1200 80">
    <path d="M0 0 L1200 0 L1200 8 Q600 64 0 8Z" fill="#fff"/>
    <path d="M0 30 Q600 80 1200 30 L1200 36 Q600 86 0 36Z" fill="#2b8fd3"/>
    <path d="M0 36 Q600 86 1200 36 L1200 80 L0 80Z" fill="#093480"/>
  </svg>
  <div class="abs f-brand"><span class="brand-dot"></span>QRN Allied Practice Partners LLC</div>
  <div class="abs socials"><span></span><span></span><span></span><span></span></div>

  <div class="abs f-head" style="left:424px">Information</div>
  <ul class="abs f-list"><li>Home</li><li>About Us</li><li>Services</li><li>Get a quote</li><li>Contact Us</li><li>Staff</li></ul>

  <div class="abs f-head" style="left:593px">Contact Us</div>
  <div class="abs f-contact">
    <div><svg viewBox="0 0 24 24"><path d="M6.6 10.8a15 15 0 0 0 6.6 6.6l2.2-2.2a1 1 0 0 1 1-.25 11 11 0 0 0 3.6.6 1 1 0 0 1 1 1V20a1 1 0 0 1-1 1A17 17 0 0 1 3 4a1 1 0 0 1 1-1h3.5a1 1 0 0 1 1 1 11 11 0 0 0 .6 3.6 1 1 0 0 1-.25 1z"/></svg>(555) 204-1187</div>
    <div><svg viewBox="0 0 24 24"><path d="M2 5h20v14H2zm2 2v.5l8 5 8-5V7z"/></svg>info@alliedpracticegroup.com</div>
    <div><svg viewBox="0 0 24 24"><path d="M12 1a8 8 0 0 0-8 8c0 6 8 14 8 14s8-8 8-14a8 8 0 0 0-8-8zm0 11a3 3 0 1 1 0-6 3 3 0 0 1 0 6z"/></svg><span>418 Harbor Lane<br>Fairview, NY 10099</span></div>
  </div>

  <div class="abs f-head" style="left:825px">Email Subscription</div>
  <div class="abs f-sub">
    Register your email address to get information
    <div class="field">Email Address</div>
    <div class="btn">SUBSCRIBE</div>
  </div>

  <div class="abs f-rule"></div>
  <div class="abs copy">Copyrights © 2018, Allied Practice Partners All Rights Reserved.</div>
</footer>

</body>
</html>
```